Investment Memorandum Document

IM for Harbourline Lending Fund - is the document that needs work

Make sure it is all done in MS WORD so that i or lawyers can edit some words if required

the IM is NOT final but its 95% of the way there. Maybe a few more pages and wording changes - but that is something i can do i guess or you can easier adjust

Just to typeset and pretty it all up - a few sample finished products have been uploaded for reference.

KTR IM is the one i like - but feel free to show off your skills

put 1.2 to 1.8 all in contrasting row tables

Target Market(s)

Individual and Institutional investors with money

Industry/Entity Type

Investment Banking

Colors

Designer to choose colors to be used in the design.

Requirements
Must have
• clear professional layout and easy on the eye
• https://www.filevaultexample.net/sh/84k3p77zrm2wqtn/BBDfpqWem3PvtsLxQZMUD41Lb?dl=0
• use the link above for high res images
Nice to have
• pictures and graphics
Should not have
• cartoons

```html
<!DOCTYPE html>
<html lang="en">
<head>
<meta charset="utf-8">
<title>Harbourline Lending Fund – Information Memorandum</title>
<link href="https://fonts.googleapis.com/css2?family=Arimo:wght@400;700&display=swap" rel="stylesheet">
<style>
:root{
  --bg:#9e9e9e;
  --paper:#ffffff;
  --ink:#3a3a3a;
  --muted:#6d6d6d;
  --accent:#2b8fd6;
  --rule:#8cc0e6;
  --sky:#c9d8e6;
  --steel:#7f93a6;
  --night:#3c4a5c;
}
*{box-sizing:border-box;margin:0;padding:0}
html,body{width:1200px;height:1000px;overflow:hidden;background:var(--bg)}
body{position:relative;font-family:"Arimo",Arial,sans-serif;color:var(--ink)}
.page{position:absolute;background:var(--paper);overflow:hidden;box-shadow:0 1px 3px rgba(0,0,0,.25)}
.p1{left:12px;top:78px;width:287px;height:404px}
.p2{left:308px;top:78px;width:288px;height:404px}
.p3{left:604px;top:78px;width:288px;height:404px}
.p4{left:904px;top:78px;width:287px;height:404px}
.p5{left:12px;top:520px;width:287px;height:404px}
.p6{left:308px;top:520px;width:288px;height:404px}
.p7{left:604px;top:520px;width:288px;height:404px}
.p8{left:904px;top:520px;width:287px;height:404px}
.photo{position:absolute}
.footer{position:absolute;left:14px;right:14px;bottom:12px;border-top:0.6px solid var(--rule);padding-top:3px;font-size:3.6px;color:var(--muted);display:flex;justify-content:space-between;font-style:italic}
.txt{position:absolute;font-size:4.1px;line-height:5.2px;text-align:justify}
.txt p{margin-bottom:3.4px}
.h-sub{color:var(--accent);font-size:4.3px;font-weight:700;text-transform:uppercase;margin:2px 0 1px}
.h-num{color:var(--accent);font-size:4.4px;font-weight:700;margin:3px 0 2px}
.h-page{color:var(--accent);font-size:7.4px;font-weight:700;margin-bottom:6px}
/* directory */
.directory{position:absolute;left:24px;top:32px;width:130px}
.directory h1{color:var(--accent);font-size:7.6px;font-weight:700;margin-bottom:12px}
.dir-role{color:var(--accent);font-size:5.4px;border-bottom:0.6px solid var(--rule);padding-bottom:2px;margin-bottom:4px}
.dir-name{font-size:4.3px;font-weight:700;margin-bottom:2px}
.dir-line{font-size:3.9px;line-height:5px;display:flex;gap:3px;margin-left:2px}
.dir-line .ico{width:4px;height:4px;flex:none;margin-top:.5px}
.dir-block{margin-bottom:9px}
/* contents */
.contents{position:absolute;left:26px;top:32px;width:232px}
.contents h1{color:var(--accent);font-size:7.4px;font-weight:700;margin-bottom:12px}
.toc-row{display:flex;justify-content:space-between;font-size:5.3px;line-height:8.8px}
/* callout */
.callout{position:absolute;left:70px;top:178px;width:186px;height:22px;border:0.7px solid #555;font-size:5px;line-height:6px;text-align:center;padding-top:4px;background:#fff}
.sign{font-weight:700}
</style>
</head>
<body>

<!-- Page: Corporate Directory -->
<section class="page p1">
  <div class="photo" role="img" aria-label="Render of a slender glass residential tower with a lattice crown, fading to white at the left" style="left:120px;top:0;width:167px;height:404px;background:linear-gradient(90deg,#fff 0%,rgba(255,255,255,0) 35%),linear-gradient(180deg,#e9eef3 0%,#b9c6d3 45%,#8899aa 80%,#c9d2dc 100%)"></div>
  <div class="directory">
    <h1>Corporate Directory</h1>
    <div class="dir-block">
      <div class="dir-role">Trustee</div>
      <div class="dir-name">Kestrel Trust and Registry Pty Ltd</div>
      <div class="dir-line"><svg class="ico" viewBox="0 0 10 10"><path d="M2 1l2 2-1 1.5c.8 1.4 1.6 2.2 3 3L7.5 6.5l2 2L8 10C4 9.5.5 6 0 2z" fill="#2b8fd6"/></svg>+613 9000 4411</div>
      <div class="dir-line"><svg class="ico" viewBox="0 0 10 10"><rect x="0.5" y="2" width="9" height="6" fill="none" stroke="#2b8fd6"/><path d="M.5 2l4.5 3.5L9.5 2" fill="none" stroke="#2b8fd6"/></svg>investors@kestreltrust.example</div>
      <div class="dir-line"><svg class="ico" viewBox="0 0 10 10"><path d="M5 10C2 6 1.5 4.8 1.5 3.5a3.5 3.5 0 017 0C8.5 4.8 8 6 5 10z" fill="#2b8fd6"/></svg>Level 4, 88 Wharf Lane, Melbourne VIC 3000</div>
    </div>
    <div class="dir-block">
      <div class="dir-role">Investment Manager</div>
      <div class="dir-name">Harbourline Asset Management Pty Ltd</div>
      <div class="dir-line"><svg class="ico" viewBox="0 0 10 10"><path d="M2 1l2 2-1 1.5c.8 1.4 1.6 2.2 3 3L7.5 6.5l2 2L8 10C4 9.5.5 6 0 2z" fill="#2b8fd6"/></svg>+613 9000 5722</div>
      <div class="dir-line"><svg class="ico" viewBox="0 0 10 10"><rect x="0.5" y="2" width="9" height="6" fill="none" stroke="#2b8fd6"/><path d="M.5 2l4.5 3.5L9.5 2" fill="none" stroke="#2b8fd6"/></svg>j.mercer@harbourline.example</div>
      <div class="dir-line"><svg class="ico" viewBox="0 0 10 10"><path d="M5 10C2 6 1.5 4.8 1.5 3.5a3.5 3.5 0 017 0C8.5 4.8 8 6 5 10z" fill="#2b8fd6"/></svg>Dockside Plaza, Tower 2<br>Level 12, 410 Pier St, Docklands VIC 3008</div>
    </div>
    <div class="dir-block">
      <div class="dir-role">Administration Manager</div>
      <div class="dir-name">Northgate Fund Services Pty Ltd</div>
      <div class="dir-line"><svg class="ico" viewBox="0 0 10 10"><path d="M2 1l2 2-1 1.5c.8 1.4 1.6 2.2 3 3L7.5 6.5l2 2L8 10C4 9.5.5 6 0 2z" fill="#2b8fd6"/></svg>+613 9000 4411</div>
      <div class="dir-line"><svg class="ico" viewBox="0 0 10 10"><rect x="0.5" y="2" width="9" height="6" fill="none" stroke="#2b8fd6"/><path d="M.5 2l4.5 3.5L9.5 2" fill="none" stroke="#2b8fd6"/></svg>investors@kestreltrust.example</div>
      <div class="dir-line"><svg class="ico" viewBox="0 0 10 10"><path d="M5 10C2 6 1.5 4.8 1.5 3.5a3.5 3.5 0 017 0C8.5 4.8 8 6 5 10z" fill="#2b8fd6"/></svg>Level 4, 88 Wharf Lane, Melbourne VIC 3000</div>
    </div>
    <div class="dir-block">
      <div class="dir-role">Australian Legal Advisors</div>
      <div class="dir-name">Brampton &amp; Lowe Lawyers</div>
      <div class="dir-line"><svg class="ico" viewBox="0 0 10 10"><path d="M2 1l2 2-1 1.5c.8 1.4 1.6 2.2 3 3L7.5 6.5l2 2L8 10C4 9.5.5 6 0 2z" fill="#2b8fd6"/></svg>+613 9000 6833</div>
      <div class="dir-line"><svg class="ico" viewBox="0 0 10 10"><path d="M5 10C2 6 1.5 4.8 1.5 3.5a3.5 3.5 0 017 0C8.5 4.8 8 6 5 10z" fill="#2b8fd6"/></svg>Alder House, 61 Market Rd</div>
      <div class="dir-line"><svg class="ico" viewBox="0 0 10 10"><path d="M5 10C2 6 1.5 4.8 1.5 3.5a3.5 3.5 0 017 0C8.5 4.8 8 6 5 10z" fill="#2b8fd6"/></svg>Melbourne VIC 3000</div>
    </div>
    <div class="dir-block">
      <div class="dir-role">Australian Tax Advisors</div>
      <div class="dir-name">Carrow Pemberton Advisory</div>
      <div class="dir-line"><svg class="ico" viewBox="0 0 10 10"><path d="M5 10C2 6 1.5 4.8 1.5 3.5a3.5 3.5 0 017 0C8.5 4.8 8 6 5 10z" fill="#2b8fd6"/></svg>Level 7, 230 Lantern St</div>
      <div class="dir-line"><svg class="ico" viewBox="0 0 10 10"><path d="M5 10C2 6 1.5 4.8 1.5 3.5a3.5 3.5 0 017 0C8.5 4.8 8 6 5 10z" fill="#2b8fd6"/></svg>Melbourne VIC 3000</div>
      <div class="dir-line"><svg class="ico" viewBox="0 0 10 10"><path d="M2 1l2 2-1 1.5c.8 1.4 1.6 2.2 3 3L7.5 6.5l2 2L8 10C4 9.5.5 6 0 2z" fill="#2b8fd6"/></svg>+613 9000 7944</div>
    </div>
  </div>
</section>

<!-- Page: Contents -->
<section class="page p2">
  <div class="contents">
    <h1>CONTENTS</h1>
    <div class="toc-row"><span>Message from the Managing Director</span><span>5</span></div>
    <div class="toc-row"><span>1. The Fund</span><span>6</span></div>
    <div class="toc-row"><span>2. The loans</span><span>10</span></div>
    <div class="toc-row"><span>3. Risks</span><span>11</span></div>
    <div class="toc-row"><span>4. Fees and costs</span><span>14</span></div>
    <div class="toc-row"><span>5. Management of the Fund</span><span>15</span></div>
    <div class="toc-row"><span>6. Taxation information</span><span>18</span></div>
    <div class="toc-row"><span>7. Additional Information</span><span>21</span></div>
    <div class="toc-row"><span>8. Application Process</span><span>25</span></div>
    <div class="toc-row"><span>9. Glossary</span><span>26</span></div>
  </div>
  <div class="photo" role="img" aria-label="Rooftop infinity pool overlooking a city skyline at dusk, fading to white at the top" style="left:0;top:200px;width:288px;height:178px;background:linear-gradient(180deg,#fff 0%,rgba(255,255,255,0) 30%),linear-gradient(180deg,#dfe6ee 0%,#9fb1c4 45%,#5d7188 70%,#7fb7cf 88%,#4f7d98 100%)"></div>
  <div class="footer" style="font-style:normal;text-transform:uppercase"><span>Harbourline Lending Fund – Information Memorandum</span><span>Page 2</span></div>
</section>

<!-- Page: Forward-looking statements -->
<section class="page p3">
  <div class="txt" style="left:10px;top:10px;width:100px">
    <p>investor or associated project to be materially different from future results, performance or achievements expressed or implied by such forward looking statements.</p>
    <p>Any forward looking statements are based on numerous assumptions regarding a project and project developer, the present and future business, the investment strategies and the markets in which a project developer will operate in the future. These forward-looking statements are current only as at the date of this IM. Accordingly, there can be no assurance that such statements, estimates or projections will be realised.</p>
    <div class="h-sub">Independent advice recommended</div>
    <p>Prospective Investors should not construe the contents of this IM as tax, legal or investment advice. The information contained in this IM is general information only and does not take into account your objectives, financial situation or needs. An investment in the Fund should be regarded as speculative and may not be appropriate for all persons or entities. You should seek professional advice and conduct your own independent investigation and analysis regarding any information contained in this IM before making any decision to invest in the Fund. You should rely on your own enquiries, in particular in obtaining your own legal, investment and tax advice in determining whether to invest in the Fund.</p>
    <div class="h-sub">No guarantee</div>
    <p>An investment in the Fund is subject to investment risk, including the loss of income and capital invested. None of the Trustee, the Investment Manager or any of their directors, officers, employees, advisers or representatives guarantee the rate of return or performance of the Fund, the meeting of the objectives of the Fund, nor do they guarantee repayment of the amount invested in the Fund.</p>
  </div>
  <div class="txt" style="left:116px;top:10px;width:100px">
    <div class="h-sub">Trustee limitation of liability</div>
    <p>Except in certain circumstances (including fraud, negligence or default by the Trustee), the Trustee enters into transactions for the Fund in its capacity as trustee of the Fund only, not in its own capacity, and its liabilities in relation to those transactions is limited to the assets of the Fund.</p>
    <div class="h-sub">Updated information</div>
    <p>The information contained in this IM may change and the IM may be updated or replaced from time to time. Unless the changed information is materially adverse to you, the Trustee may not always update or replace this IM to reflect the changed information. Updated information can be obtained by contacting the Trustee on +613 9000 4411.</p>
    <div class="h-sub">Confidentiality</div>
    <p>This IM is confidential and is provided to prospective Investors for them to consider investing in the Fund. Its use for any other purpose is not permitted. It may not be reproduced or redistributed, in whole or in part, and its contents may not be disclosed to any person.</p>
    <div class="h-sub">Glossary</div>
    <p>Certain capitalised words and expressions used in this IM are defined in the Glossary. All references to dollar amounts in this IM are to Australian Dollars (AUD), unless otherwise stated.</p>
  </div>
  <div class="photo" role="img" aria-label="Close view of a pale residential tower facade with balconies" style="left:222px;top:0;width:66px;height:404px;background:linear-gradient(90deg,#fff 0%,rgba(255,255,255,0) 40%),linear-gradient(180deg,#eceff2 0%,#c3c9cf 50%,#9aa3ab 100%)"></div>
  <div class="footer"><span>Harbourline Lending Fund – Information Memorandum</span><span style="font-style:normal">PAGE 4</span></div>
</section>

<!-- Page: Risks -->
<section class="page p4">
  <div class="txt" style="left:10px;top:10px;width:128px">
    <p>As the Fund will make loans to entities controlled by Harbourline Capital Group, a related party of the Investment Manager, there is an inherent conflict that arises in respect of the loans made by the Fund. This risk is mitigated by the fact that the loans must be made in accordance with the Lending Guidelines and the Trustee reviews the loans to ensure that they are made in accordance with the Lending Guidelines and this IM before it executes the loan documents.</p>
    <div class="h-num">Risks associated with the solvency and financial position of the Investment Manager and borrowers</div>
    <p>The financial performance of the loans will be impacted by the financial performance of the Investment Manager, the SPVs, the borrowers under loans from the SPVs, and the success of the projects undertaken by the relevant project development entities.</p>
  </div>
  <div class="txt" style="left:148px;top:10px;width:128px">
    <p>If the Investment Manager either becomes insolvent or encounters financial difficulties, which mean that it is unable to perform its role under the Investment Management Agreement, then the Trustee will most likely need to terminate the Investment Management Agreement and recover any unpaid or future Fees and Costs from the Fund. If that were to occur, then the Trustee would either need to find a replacement investment manager or wind up the Fund.</p>
    <p>This could result in you suffering a loss or a diminished return on your investment in the Fund.</p>
    <p>If the SPVs or project development entities become insolvent or face financial difficulties, then the Fund may suffer losses and you may lose some or all of your investment as a result. It is likely that the SPVs and project development entities will be thinly capitalised.</p>
  </div>
  <div class="photo" role="img" aria-label="Aerial render of a rooftop terrace with a circular pool, observation wheel and city behind at dusk" style="left:0;top:190px;width:287px;height:188px;background:linear-gradient(180deg,#c7d2de 0%,#8a9bb0 30%,#3f4e62 60%,#5f8aa3 78%,#2e3a48 100%)"></div>
  <div class="callout">We strongly recommend that Investors obtain independent financial advice before investing in the Fund.</div>
  <div class="footer"><span>Harbourline Lending Fund – Information Memorandum</span><span style="font-style:normal">PAGE 13</span></div>
</section>

<!-- Page: Application Process -->
<section class="page p5">
  <div class="txt" style="left:14px;top:16px;width:259px">
    <div class="h-page">9.&nbsp;&nbsp;&nbsp;Application Process</div>
    <p>After reviewing this IM, Investors can invest in Cash Units or Loan Units by completing the Application Form and paying their application money. Payments must be made via EFT/POS (bank transfer) or bank cheque.</p>
    <p>Once the completed Application Form and application money is received by the Trustee and the Trustee accepts the application, Investors will be issued with Units. Units will be issued within 5 Business Days of the end of each calendar month in which the completed Application Form and corresponding application money is received, or at any other time at the Trustee's absolute discretion.</p>
    <p>Application monies are held in the Fund's Application Account prior to being allocated to Cash Units. Please note that no interest will be earned by Investors on monies that are held in the Application Account.</p>
  </div>
  <div class="photo" role="img" aria-label="Waterfront render of curved residential buildings beside a marina under a blue sky" style="left:0;top:208px;width:287px;height:170px;background:linear-gradient(180deg,#fff 0%,rgba(255,255,255,0) 22%),linear-gradient(180deg,#e4ebf2 0%,#9fb8cf 40%,#5c7690 70%,#3f6f8e 100%)"></div>
  <div class="footer"><span>Harbourline Lending Fund – Information Memorandum</span><span style="font-style:normal">PAGE 26</span></div>
</section>

<!-- Page: Taxation information -->
<section class="page p6">
  <div class="txt" style="left:14px;top:16px;width:260px">
    <div class="h-page">7.&nbsp;&nbsp;&nbsp;Taxation information</div>
    <p>The Trustee has engaged Carrow Pemberton Advisory, an award-winning and leading mid-sized chartered accounting group, to provide a general outline of the Australian tax implications of purchasing Units pursuant to this IM as well as the holding and disposing of such units, which is contained in the following letter.</p>
    <p>Taxation laws are both complex and subject to change and Investors should obtain their own advice taking account of their own circumstances.</p>
    <p>19 October 2018</p>
    <p>The Directors<br>Kestrel Trust and Registry Pty Ltd as Trustee for<br>Harbourline Lending Fund<br>Level 4, 88 Wharf Lane<br>Melbourne, Victoria 3000</p>
    <p>Dear Directors</p>
    <p class="sign">Australian Taxation Implications for Investors in the Harbourline Lending Fund</p>
    <p>As requested, this letter has been prepared for inclusion in the Information Memorandum dated on or around 19 October 2018, in relation to the issue of units in the Harbourline Lending Fund (the Fund).</p>
    <p>This letter provides a general summary for Australian resident and non-resident investors (the Investors) who subscribe for units pursuant to the Information Memorandum and hold the units on capital account for Australian income tax purposes. It does not attempt to address all of the Australian tax consequences that may be relevant to the Investors.</p>
    <p>The opinion is general in nature because the tax implications for each Investor may vary depending on their particular circumstances. Accordingly, it is recommended that each Investor seeks their own professional advice regarding the taxation implications before making any investment or other decision in relation to the units in the Fund. This taxation opinion is not, and is not intended to be, taxation advice to any particular Investor.</p>
    <p>This opinion is based on the Income Tax Assessment Act 1936 (ITAA 1936) and the Income Tax Assessment Act 1997 (ITAA 1997) (collectively referred to as the Tax Law) as applicable at the date of this opinion.</p>
    <div class="h-num">1. Tax Treatment of the Fund</div>
    <p>As the Fund is a unit trust, it will be treated as "flow through" entity for Australian income tax purposes. That is, the taxable income of the Fund will be subject to Australian tax in hands of Investors, not the Fund on the basis that the Investors are made presently entitled to all of the income of the Fund at the end of each income year, and the activities of the Fund are limited to eligible investment businesses such that the Fund should not constitute a public trading trust.</p>
    <p>We understand the Fund offers Investors the opportunity to acquire interests in Cash Units and Loan Units. Typically, Cash Units are referable to a basic deposit product including cash management accounts and term deposits and Loan Units are referable to a portfolio of loans which may comprise loans that may be unsecured or secured by a mixture of first mortgages, second mortgages or other security interest.</p>
    <div class="h-num">2. Tax Treatment of Investors</div>
    <p>The section contains an outline of the Australian income tax implications that will generally apply to Investors that acquire Fund units on capital account.</p>
    <div class="h-num">2.1 Australian Resident Investors</div>
    <p>From time to time, Investors who are made presently entitled to the distributable income of the Fund will receive trust distributions from the Fund, in proportion to their entitlements to that distributable income.</p>
  </div>
  <div class="footer" style="font-style:normal;text-transform:uppercase"><span>Harbourline Lending Fund – Information Memorandum</span><span>Page 18</span></div>
</section>

<!-- Page: Taxation continued -->
<section class="page p7">
  <div class="txt" style="left:14px;top:14px;width:260px">
    <p>In this regard, Australian resident Investors should recognise their share of the distributable income, which is likely primarily in the form of interest income, to be included in their assessable income.</p>
    <p>The redemption or transfer of units will constitute a disposal by an Investor for tax purposes. If the Investor holds their units on capital account, any gain made by the Investor on disposal will be subject to capital gains tax (CGT). If the Investor makes a capital loss, it may be used to offset capital gains derived in the current or a future tax year. We understand that it is intended by the Trustee that the unit price is to be issued at $1.00 per unit but this may not always be the case as the unit price is based on underlying value of the assets referable to the particular class of units.</p>
    <p>A CGT discount may be available on the capital gain on units held for 12 months or more by individual, trusts or complying superannuation entities. Companies are not eligible for CGT discount. For individual and trusts, the discount is 50%. For complying superannuation entities, the discount is 33.33%.</p>
    <div class="h-num">2.2 Non-Resident Investors</div>
    <p>Given the intention is that the distributable income of the Fund will primarily represent interest income, non-resident Investors should only be subject to 10% final interest withholding tax (IWHT) on any income distribution received. This tax treatment applies irrespective of whether the Fund is classified as a Managed Investment Trust (MIT) for tax purposes.</p>
    <p>That is, the Trustee is required to withhold a 10% IWHT to the Australian Taxation Office (ATO) and non-resident Investors are not required to lodge an Australian income tax return if interest income is the only source of income as the IWHT is treated as a final tax liability in Australia.</p>
    <p>If any income from the Fund is not interest, dividend or royalties income, non-resident Investors may either be subject to the general trust withholding provisions or the MIT withholding provisions. Investors should seek their own advice on these matters.</p>
    <p>Any capital gain or capital loss resulting from a disposal or redemption of units in the Fund by a non-resident Investor will be disregarded if a non-resident Investor holds less than 10% of the units in the Fund or the Fund does not hold majority investments in Australian real property.</p>
    <p>Each non-resident Investor, however, should seek their own advice when they seek to dispose or redeem the units.</p>
    <div class="h-num">3. Annual reporting</div>
    <p>As the Fund is likely to constitute an Investment Body, the Fund will be required to provide certain distribution information (including tax components) to the ATO on an annual basis by lodging the Annual Investment Income Report (AIIR).</p>
    <p>The Trust will also provide an annual tax distribution statement to Investors in accordance with the ATO's guidelines for Managed Funds. The tax distribution statement will reconcile the cash distribution provided to the Investor with the taxable distribution for that income year.</p>
    <div class="h-num">4. Attribution Managed Investment Trust (AMIT) regime</div>
    <p>The Government has enacted a tax regime for certain managed investment trusts known as the Attribution Managed Investment Trust (AMIT) Rules. The AMIT Rules remove a number of uncertainties for Trustees and Investors and facilitate fair and reasonable tax outcomes for Investors.</p>
    <p>The AMIT Rules do not apply automatically to all MITs. The Trustee will make an assessment of whether the Fund qualifies as an AMIT and whether it will make an election to apply the AMIT Rules to the Fund.</p>
    <div class="h-num">5. Goods and Services Tax</div>
    <p>GST should not apply on the acquisition and disposal of units as well as cash distribution from the Fund to the Investors.</p>
    <div class="h-num">6. Change of Tax residency</div>
  </div>
  <div class="footer"><span>Harbourline Lending Fund – Information Memorandum</span><span style="font-style:normal">PAGE 20</span></div>
</section>

<!-- Page: Taxation closing -->
<section class="page p8">
  <div class="txt" style="left:14px;top:14px;width:259px">
    <p>We recommend that each Investor seeks professional advice on their residency status if there may be a change in their tax residency through the course of their investments and the associated tax implications relevant for their circumstances.</p>
    <div class="h-num">7. Tax File Number (TFN)</div>
    <p>Australian resident Investors may choose not to provide the Trustee with their TFNs. However, if a TFN is not quoted, or no appropriate TFN exemption is provided, the Trustee is required to deduct tax from any income distribution entitlement at the highest marginal tax rate plus Medicare Levy.</p>
    <p>Yours sincerely</p>
    <p style="margin-top:10px"><span class="sign">Daniel Forsythe</span><br>Director</p>
    <p>Carrow Pemberton Advisory (Vic) Pty Ltd<br>Chartered Accountants</p>
  </div>
  <div class="footer"><span>Harbourline Lending Fund – Information Memorandum</span><span style="font-style:normal">PAGE 21</span></div>
</section>

</body>
</html>
```